The Neighbors Together Project

For submission to Lantern Campaign 2024
Need both Color and Black and White Versions
TITLE The Neighbors Together Project
Slogan; "Neighbors Together, one road...one Heart, just a different stride" -JT Pellow copyrights
Logo in Color and Logo in Black and White
Back of flyer will be The Field of Quiet Lanterns poem -JT Pellow
VOTE BLUE 2024 Header or Footer

I just want to thank you all for your participation in The Neighbors Together Project. In the next few days I will be reducing the choices down to 10. Id like for all of you to know Ive enjoyed seeing so many options and views on the Flyer. Mainly, I wanted to say to those who don't make the cut that I appreciate the work you've done.

LM Dorsey

```html
<!DOCTYPE html>
<html lang="en">
<head>
<meta charset="utf-8">
<title>The Neighbors Together Project – Lantern Campaign 2024 Flyer</title>
<link rel="stylesheet" href="https://fonts.googleapis.com/css2?family=Montserrat:wght@800;900&family=Poppins:wght@400;700&family=Quicksand:wght@500;600&display=swap">
<style>
  :root {
    --page: #eeefef;
    --navy: #0f1f4d;
    --navy-deep: #0a1638;
    --white: #ffffff;
    --blue: #1f78d6;
    --red: #e8203a;
    --flag-blue: #2a3f8f;
    --flag-red: #d8323f;
    --flag-white: #f4eef0;
  }
  * { box-sizing: border-box; margin: 0; padding: 0; }
  html, body {
    width: 1200px; height: 736px; overflow: hidden;
    background: var(--page);
  }
  body { position: relative; font-family: "Quicksand", sans-serif; color: var(--white); }

  .flyer {
    position: absolute; top: 119px;
    width: 353px; height: 499px;
    background: radial-gradient(ellipse at 60% 40%, #162a5e 0%, var(--navy) 55%, var(--navy-deep) 100%);
    overflow: hidden;
  }
  .flyer--front { left: 172px; }
  .flyer--back { left: 665px; }

  /* Front */
  .flag-photo {
    position: absolute; left: 0; top: 0; width: 108px; height: 100%;
    background:
      linear-gradient(90deg, rgba(15,31,77,0) 70%, var(--navy) 100%),
      linear-gradient(180deg, var(--flag-blue) 0%, var(--flag-blue) 60%, var(--flag-white) 70%, var(--flag-red) 80%, var(--flag-white) 90%, var(--flag-red) 100%);
  }
  .logo-panel {
    position: absolute; left: 120px; top: 57px; width: 205px; height: 193px;
    border: 2px solid var(--white); border-radius: 18px; padding: 5px;
  }
  .logo-panel__inner {
    width: 100%; height: 100%; background: var(--white); border-radius: 13px;
    display: flex; flex-direction: column; align-items: center; justify-content: center; gap: 10px;
  }
  .logo-panel__mark { width: 34px; height: 34px; border-radius: 50%; background: var(--navy); }
  .logo-panel__name {
    font-family: "Poppins", sans-serif; font-weight: 700; font-size: 17px; line-height: 1.15;
    color: var(--navy); text-align: center; text-transform: uppercase; letter-spacing: 0.5px;
  }

  /* Vote headline: plain set type */
  .vote-block { position: absolute; left: 0; width: 100%; text-align: center; }
  .vote-line {
    font-family: "Montserrat", sans-serif; font-weight: 900; line-height: 1;
    display: block; letter-spacing: 1px;
  }
  .vote-line--white { color: var(--white); }
  .vote-line--blue { color: var(--blue); }

  .flyer--front .vote-block { top: 298px; }
  .flyer--front .vote-line { font-size: 50px; }
  .flyer--front .vote-line + .vote-line { margin-top: 3px; }

  .site-line { border-top: 1.5px solid var(--white); margin: 0 auto; }
  .site {
    display: flex; align-items: center; justify-content: center; gap: 3px;
    font-family: "Quicksand", sans-serif; font-weight: 600; color: var(--white);
    white-space: nowrap;
  }
  .star { line-height: 1; }
  .star--red { color: var(--red); }
  .star--blue { color: var(--blue); }
  .star--white { color: var(--white); }

  .flyer--front .site-line { width: 156px; margin-top: 8px; }
  .flyer--front .site { font-size: 6.5px; margin-top: 3px; }
  .flyer--front .site .star { font-size: 7px; }

  /* Back */
  .poem-title {
    position: absolute; left: 70px; top: 50px; width: 215px; height: 38px;
    border: 1.5px solid var(--white); text-align: center; padding-top: 3px;
  }
  .poem-title__name { font-family: "Poppins", sans-serif; font-weight: 700; font-size: 15px; line-height: 18px; }
  .poem-title__author { font-family: "Poppins", sans-serif; font-weight: 400; font-size: 10px; line-height: 12px; }
  .poem {
    position: absolute; left: 0; top: 104px; width: 100%; text-align: center;
    font-size: 11px; font-weight: 500; line-height: 13px;
  }
  .poem p + p { margin-top: 13px; }

  .flyer--back .vote-block { top: 381px; }
  .flyer--back .vote-line--white { font-size: 32px; }
  .flyer--back .vote-row { display: block; margin-top: 2px; font-size: 26px; }
  .flyer--back .vote-row .vote-line { display: inline; font-size: 26px; }
  .flyer--back .site-line { width: 268px; margin-top: 9px; }
  .flyer--back .site { font-size: 11px; margin-top: 3px; gap: 6px; }
  .flyer--back .site .star { font-size: 13px; }
</style>
</head>
<body>

<section class="flyer flyer--front">
  <div class="flag-photo" role="img" aria-label="Photograph of a draped American flag with stars and stripes"></div>

  <div class="logo-panel">
    <div class="logo-panel__inner">
      <span class="logo-panel__mark"></span>
      <span class="logo-panel__name">Neighbors<br>Together</span>
    </div>
  </div>

  <div class="vote-block">
    <span class="vote-line vote-line--white">VOTE</span>
    <span class="vote-line vote-line--blue">BLUE</span>
    <span class="vote-line vote-line--white">2024</span>
    <div class="site-line"></div>
    <div class="site">
      <span class="star star--red">★</span><span class="star star--blue">★</span><span class="star star--white">★</span>
      <span>www.neighborstogetherproject.org</span>
      <span class="star star--white">★</span><span class="star star--blue">★</span><span class="star star--red">★</span>
    </div>
  </div>
</section>

<section class="flyer flyer--back">
  <header class="poem-title">
    <h1 class="poem-title__name">Field of Quiet Lanterns</h1>
    <p class="poem-title__author">By JT Pellow</p>
  </header>

  <div class="poem">
    <p>When evening settles on the meadow grass<br>and porch lights flicker one by one,<br>we gather where the old roads pass.</p>
    <p>Each lantern carried by a different hand,<br>each flame a story, small and bright,<br>together lighting up the land.</p>
    <p>Some walked in slowly, some came far,<br>from distant harbors, hills and plains,<br>and found a home beneath this star.</p>
    <p>We share the bread, we mend the fence,<br>we keep the watch through winter nights,<br>a neighbor's hand our best defense.</p>
    <p>So lift your lantern, hold it high,<br>one road, one heart, a different stride,<br>a field of light against the sky.</p>
  </div>

  <div class="vote-block">
    <span class="vote-line vote-line--white">VOTE</span>
    <span class="vote-row"><span class="vote-line vote-line--blue">BLUE</span> <span class="vote-line vote-line--white">2024</span></span>
    <div class="site-line"></div>
    <div class="site">
      <span class="star star--red">★</span><span class="star star--blue">★</span><span class="star star--white">★</span>
      <span>www.neighborstogetherproject.org</span>
      <span class="star star--white">★</span><span class="star star--blue">★</span><span class="star star--red">★</span>
    </div>
  </div>
</section>

</body>
</html>
```